Need help in designing new business card utilizing our new logo.

BuildMark Solutions works with Construction Business Owners, Managers & IT Professionals to strengthen software usage and increase user productivity.

Our Construction Accounting and Mobile Field Management Software Clients engage with us in the following areas:

New Software Implementations
Software Re-Implementations
Redesigning Software Usage at the User Level
Project Coordination & Management
Continued Software Support

Old tag line:
Weighing Options - Implementing Solutions

www.buildmark-solutions.example

Ridge 4 is a product, but not needed for a new business card.

```html
<!DOCTYPE html>
<html lang="en">
<head>
<meta charset="utf-8">
<title>BuildMark Solutions – Business Card</title>
<link href="https://fonts.googleapis.com/css2?family=Montserrat:wght@600&family=Oswald:wght@500&family=Didact+Gothic&display=swap" rel="stylesheet">
<style>
  :root {
    --brand-blue: #2e35a3;
    --ink: #1f1f24;
    --paper: #ffffff;
    --stage: #e9eaee;
    --rule: #2a2a2e;
  }
  * { box-sizing: border-box; margin: 0; padding: 0; }
  html, body {
    width: 1200px; height: 800px; overflow: hidden;
    background: var(--stage);
  }
  .canvas { position: relative; width: 1200px; height: 800px; }
  .card {
    position: absolute; top: 240px;
    width: 560px; height: 320px;
    box-shadow: 0 6px 20px rgba(0,0,0,.18);
    overflow: hidden;
  }
  /* Front */
  .card-front { left: 30px; background: var(--brand-blue); }
  .card-front .map-texture {
    position: absolute; inset: 0;
    background: radial-gradient(ellipse at 45% 50%, rgba(255,255,255,.05), rgba(0,0,0,.04) 70%);
  }
  .wordmark {
    position: absolute; display: flex; align-items: center; gap: 14px;
    font-family: "Montserrat", sans-serif; font-weight: 600;
    letter-spacing: .06em; text-transform: uppercase; line-height: 1.1;
  }
  .wordmark .mark-square { flex: none; }
  .card-front .wordmark {
    left: 0; right: 0; top: 128px; justify-content: center;
    color: var(--paper); font-size: 28px;
  }
  .card-front .mark-square { width: 44px; height: 44px; background: var(--paper); }

  /* Back */
  .card-back { left: 610px; background: var(--paper); }
  .card-back .wordmark {
    left: 34px; top: 46px; color: var(--brand-blue); font-size: 22px;
  }
  .card-back .mark-square { width: 40px; height: 40px; background: var(--brand-blue); }
  .edge-tab {
    position: absolute; right: -10px; top: 44px;
    width: 20px; height: 44px; border-radius: 10px;
    background: var(--brand-blue);
  }
  .holder {
    position: absolute; right: 40px; top: 50px; text-align: right;
  }
  .holder-name {
    font-family: "Oswald", sans-serif; font-weight: 500;
    font-size: 22px; letter-spacing: .02em; color: var(--ink);
    text-transform: uppercase; line-height: 1;
  }
  .holder-role {
    font-family: "Montserrat", sans-serif; font-weight: 600;
    font-size: 11px; color: var(--ink); margin-top: 3px;
  }
  .divider-main {
    position: absolute; left: 34px; right: 40px; top: 118px;
    height: 1px; background: var(--rule);
  }
  .address {
    position: absolute; right: 40px; top: 140px; text-align: right;
    font-family: "Didact Gothic", sans-serif; font-style: normal;
    font-size: 12.5px; line-height: 1.5; color: var(--ink);
  }
  .divider-contact {
    position: absolute; left: 34px; width: 240px; top: 208px;
    height: 1px; background: var(--rule);
  }
  .contact-list {
    position: absolute; left: 34px; top: 218px; list-style: none;
    font-family: "Didact Gothic", sans-serif; font-size: 12.5px;
    color: var(--ink); line-height: 1.55;
  }
  .contact-list li { display: flex; align-items: center; gap: 10px; }
  .contact-list svg { width: 11px; height: 11px; flex: none; fill: var(--brand-blue); }
  .contact-list .web-domain { color: var(--brand-blue); }
</style>
</head>
<body>
<main class="canvas">
  <section class="card card-front" aria-label="Card front">
    <div class="map-texture" role="img" aria-label="Faint world map texture across the card"></div>
    <div class="wordmark"><span class="mark-square"></span><span>BuildMark<br>Solutions</span></div>
  </section>

  <section class="card card-back" aria-label="Card back">
    <div class="wordmark"><span class="mark-square"></span><span>BuildMark<br>Solutions</span></div>
    <span class="edge-tab"></span>
    <div class="holder">
      <p class="holder-name">Dana R. Whitfield</p>
      <p class="holder-role">Owner</p>
    </div>
    <div class="divider-main"></div>
    <address class="address">
      48 Linden Avenue - Suite 12<br>
      Maple Falls NY 10000
    </address>
    <div class="divider-contact"></div>
    <ul class="contact-list">
      <li><svg viewBox="0 0 12 12" aria-hidden="true"><path d="M2.5 1l2 2.3-1 1.2a7 7 0 0 0 4 4l1.2-1 2.3 2-1.3 1.5C5.5 11 1 6.5 1 2.3z"/></svg>800-555-0142 ext.100</li>
      <li><svg viewBox="0 0 12 12" aria-hidden="true"><path d="M3 0h6a1 1 0 0 1 1 1v10a1 1 0 0 1-1 1H3a1 1 0 0 1-1-1V1a1 1 0 0 1 1-1zm0 1.5v8h6v-8zM6 10.2a.6.6 0 1 0 0 1.2.6.6 0 0 0 0-1.2z"/></svg>518-555-0173</li>
      <li><svg viewBox="0 0 12 12" aria-hidden="true"><path d="M0 2h12v1L6 7 0 3zM0 4.3l6 4 6-4V10H0z"/></svg>dana.whitfield@buildmark-solutions.example</li>
      <li><svg viewBox="0 0 12 12" aria-hidden="true"><path d="M7 0a5 5 0 1 1-3 9l-2.6 2.6-1-1L3 8a5 5 0 0 1 4-8zm0 1.5a3.5 3.5 0 1 0 0 7 3.5 3.5 0 0 0 0-7z"/></svg><span>www.<span class="web-domain">buildmark-solutions</span>.example</span></li>
    </ul>
  </section>
</main>
</body>
</html>
```